We need letterhead, Business Cards, and envelops designed. We have attached a design of our logo and a sample of letterhead idea that was started but never perfected, it is only an idea for the letterhead if you can design something better we may love that also we are open to change.
We want a design that looks professional in style. we are a non profit trade association in the construction industry. the green color in the attached design represent green building, and we like that. also if you just want to enhance the letterhead sample that we attached that would be fine also.
Thanks and good luck
also the name that should show on the first business cards should be Morgan Feltwick, Director are web address is www.pvtrn.org

```html
<!DOCTYPE html>
<html lang="en">
<head>
<meta charset="utf-8">
<title>PVTRN Letterhead</title>
<link rel="stylesheet" href="https://fonts.googleapis.com/css2?family=Questrial&display=swap">
<style>
  :root {
    --band-green: #4a8549;
    --paper-green: #deebb8;
    --band-text: #e4efdc;
    --ink: #333333;
    --accent: #4a8549;
  }
  * { margin: 0; padding: 0; box-sizing: border-box; }
  html, body {
    width: 849px;
    height: 1200px;
    overflow: hidden;
  }
  body {
    font-family: "Questrial", sans-serif;
    background: var(--paper-green);
  }
  .letterhead {
    position: relative;
    width: 849px;
    height: 1200px;
    background: var(--paper-green);
  }
  .side-band {
    position: absolute;
    left: 0;
    top: 0;
    width: 203px;
    height: 1200px;
    background: var(--band-green);
  }
  .contact {
    position: absolute;
    left: 20px;
    top: 90px;
    color: var(--band-text);
    font-size: 16.5px;
    line-height: 20.5px;
    font-style: normal;
    white-space: nowrap;
  }
  .contact .gap { height: 20.5px; }
  .brand {
    position: absolute;
    left: 306px;
    top: 100px;
    width: 446px;
    color: var(--ink);
  }
  .brand-row {
    display: flex;
    align-items: center;
    gap: 20px;
  }
  .brand-mark {
    width: 58px;
    height: 58px;
    background: var(--accent);
    flex: none;
  }
  .brand-name {
    font-size: 112px;
    line-height: 104px;
    letter-spacing: 3px;
  }
  .brand-full {
    margin-top: 4px;
    font-size: 20px;
    line-height: 24px;
    letter-spacing: 0.6px;
    white-space: nowrap;
  }
</style>
</head>
<body>
  <main class="letterhead">
    <aside class="side-band">
      <address class="contact">
        <div>Address</div>
        <div>1187 Larkmoor Avenue</div>
        <div>Fairhaven, State ZIP</div>
        <div class="gap"></div>
        <div>tel: 555-218-4470</div>
        <div>fax: 555-218-4471</div>
        <div>url: www.pvtrn.org</div>
      </address>
    </aside>
    <header class="brand">
      <div class="brand-row">
        <span class="brand-name">PVTRN</span>
        <span class="brand-mark" aria-hidden="true"></span>
      </div>
      <div class="brand-full">Pacific Valley Trades Registry Network</div>
    </header>
  </main>
</body>
</html>
```